Brintel Works - Fast, Efficient and Gas Mainteance for Domestic, Commercial and Industrial clients

We are in the process of purchasing a new business and would like to get a new logo and business card.
Business is a gas maintenance business that also does new gas installations.
Has been established since 1988.
Services include:
Install all types of gas appliances & equipment inc. hot water units
Maintain / repair / replace all types of gas appliances & equipment

Target Market(s)

Domestic, Commercial and Industrial clients

Industry/Entity Type

Business

Contact Information for Business Card

admin@brintelworks.com.au
07 3918 4726
Brintel Works PTY LTD

Logo Text

Gas Fitting & Plumbing Maintenance Specialists

Font styles to use
Sans Serif

Requirements
Must have
• Logo
• Business name, contact number, email address, web address
• Domestic | Commercial | Industrial Est Since 1988
Nice to have
• Possibly a black card with a flame logo to one side
Should not have
• Spelling errors

```html
<!DOCTYPE html>
<html lang="en">
<head>
<meta charset="utf-8">
<title>Brintel Works business card</title>
<link rel="stylesheet" href="https://fonts.googleapis.com/css2?family=Tinos:wght@700&family=Open+Sans:wght@400;600&family=Pinyon+Script&display=swap">
<style>
  :root {
    --page: #ece9e4;
    --card-dark: #000000;
    --band-light: #e8e8e8;
    --brand-red: #e6452b;
    --icon-orange: #f0502e;
    --text-grey: #4a4a4a;
    --muted-grey: #a9a9a9;
    --mark-grey: #c9c9c9;
    --white: #ffffff;
  }
  * { box-sizing: border-box; margin: 0; padding: 0; }
  html, body { width: 1189px; height: 1200px; overflow: hidden; background: var(--page); }
  .canvas { position: relative; width: 1189px; height: 1200px; }
  .card {
    position: absolute; left: 140px; width: 918px; height: 524px;
    background: var(--card-dark); overflow: hidden;
    box-shadow: 0 6px 14px rgba(0,0,0,.25);
  }
  .card--front { top: 45px; }
  .card--back { top: 624px; }

  .front-band { position: absolute; left: 0; top: 0; width: 100%; height: 215px; background: var(--band-light); }
  .band-mark { position: absolute; left: 30px; top: 104px; width: 46px; height: 46px; border-radius: 50%; background: var(--mark-grey); }
  .brand-name {
    position: absolute; font-family: "Tinos", "Times New Roman", serif; font-weight: 700;
    color: var(--brand-red); white-space: nowrap; line-height: 1;
  }
  .front-band .brand-name { left: 101px; top: 52px; font-size: 41px; letter-spacing: .5px; }
  .brand-name small { font-size: .3em; margin-left: 8px; }
  .tagline { position: absolute; font-family: "Open Sans", Arial, sans-serif; font-weight: 600; white-space: nowrap; }
  .front-band .tagline { left: 101px; top: 100px; font-size: 25px; color: var(--text-grey); }
  .sectors { position: absolute; font-family: "Open Sans", Arial, sans-serif; white-space: nowrap; display: flex; align-items: baseline; gap: 14px; }
  .front-band .sectors { left: 101px; top: 141px; font-size: 14px; color: var(--text-grey); }
  .est { font-family: "Pinyon Script", cursive; }
  .front-band .est { font-size: 22px; color: #777; }

  .product-photo {
    position: absolute; left: 553px; top: 0; width: 365px; height: 253px;
    background: linear-gradient(135deg, #5a5a5a 0%, #3b3b3b 35%, #b14a1e 50%, #3b3b3b 62%, #b8bcc0 78%, #d8dadc 100%);
  }

  .contact-list { position: absolute; left: 57px; top: 283px; list-style: none; }
  .contact-item { display: flex; align-items: center; height: 44px; font-family: "Open Sans", Arial, sans-serif; font-size: 29px; color: var(--white); white-space: nowrap; }
  .contact-icon { width: 21px; height: 21px; margin-right: 24px; flex: none; }

  .back-mark { position: absolute; left: 78px; top: 158px; width: 180px; height: 180px; border-radius: 50%; background: var(--mark-grey); }
  .card--back .brand-name { left: 298px; top: 207px; font-size: 58px; }
  .card--back .brand-name small { font-size: .42em; margin-left: 14px; }
  .card--back .tagline { left: 298px; top: 272px; font-size: 23px; font-weight: 400; color: var(--muted-grey); }
  .card--back .sectors { left: 298px; top: 314px; font-size: 18px; color: var(--white); }
  .card--back .est { font-size: 25px; color: var(--white); }
</style>
</head>
<body>
<div class="canvas">

  <section class="card card--front">
    <div class="front-band">
      <div class="band-mark"></div>
      <div class="brand-name">BRINTEL WORKS<small>PTY LTD</small></div>
      <div class="tagline">Gas fitting &amp; Plumbing Specialists</div>
      <div class="sectors"><span>Domestic | Commercial | Industrial</span><span class="est">Est Since 1988</span></div>
    </div>
    <div class="product-photo" role="img" aria-label="Photo of a wood heater with flames and two hot water cylinders"></div>

    <ul class="contact-list">
      <li class="contact-item">
        <svg class="contact-icon" viewBox="0 0 20 20"><rect width="20" height="20" fill="var(--icon-orange)"/><path d="M6 4l2.5 0 1 3.5-1.6 1.2a7 7 0 0 0 3.4 3.4l1.2-1.6 3.5 1v2.5c0 .6-.4 1-1 1A11 11 0 0 1 5 5c0-.6.4-1 1-1z" fill="#000"/></svg>
        07 3918 4726
      </li>
      <li class="contact-item">
        <svg class="contact-icon" viewBox="0 0 20 20"><rect width="20" height="20" fill="var(--icon-orange)"/><rect x="6" y="3.5" width="8" height="4" fill="#000"/><rect x="3.5" y="8" width="13" height="6" fill="#000"/><rect x="6" y="12" width="8" height="4.5" fill="#000" stroke="var(--icon-orange)" stroke-width="1"/></svg>
        07 3918 4752
      </li>
      <li class="contact-item">
        <svg class="contact-icon" viewBox="0 0 20 20"><rect width="20" height="20" fill="var(--icon-orange)"/><circle cx="10" cy="10" r="6" fill="none" stroke="#000" stroke-width="1.8"/><path d="M4 10h12M10 4c-3 3-3 9 0 12M10 4c3 3 3 9 0 12" fill="none" stroke="#000" stroke-width="1.3"/></svg>
        www.brintelworks.com.au
      </li>
      <li class="contact-item">
        <svg class="contact-icon" viewBox="0 0 20 20"><rect width="20" height="20" fill="var(--icon-orange)"/><rect x="3.5" y="5.5" width="13" height="9" fill="#000"/><path d="M3.5 5.5l6.5 5 6.5-5" fill="none" stroke="var(--icon-orange)" stroke-width="1.2"/></svg>
        admin@brintelworks.com.au
      </li>
      <li class="contact-item">
        <svg class="contact-icon" viewBox="0 0 20 20"><rect width="20" height="20" fill="var(--icon-orange)"/><path d="M10 3.5a4.5 4.5 0 0 1 4.5 4.5c0 3.5-4.5 8.5-4.5 8.5S5.5 11.5 5.5 8A4.5 4.5 0 0 1 10 3.5z" fill="#000"/><circle cx="10" cy="8" r="1.6" fill="var(--icon-orange)"/></svg>
        PO Box 2846, Kedron Bay, QLD 4031
      </li>
    </ul>
  </section>

  <section class="card card--back">
    <div class="back-mark"></div>
    <div class="brand-name">Brintel Works<small>PTY LTD</small></div>
    <div class="tagline">Gas Fitting &amp; Plumbing Specialists</div>
    <div class="sectors"><span>Domestic | Commercial | Industrial</span><span class="est">Est Since 1988</span></div>
  </section>

</div>
</body>
</html>
```